BOLD & MINIMALIST DESIGN NEEDED

We want a very bold but minimalistic business card design that is impactful and utilizes both sides of the business card. Our current logo is included for your use.

We want bold fonts and good use of negative space. We don't want the logo to overpower the design.

Target Market(s)

Professionals who are building new commercial buildings.

Industry/Entity Type

Construction

Contact Information for Business Card

Name, Title, email, office phone, cell phone, website

Font styles to use
Serif
Sans Serif

Requirements
Must have
• Bold design!

```html
<!DOCTYPE html>
<html lang="en">
<head>
<meta charset="utf-8">
<title>Ridgeline Design + Build — Business Card</title>
<link href="https://fonts.googleapis.com/css2?family=Poppins:wght@400;500;600;800&display=swap" rel="stylesheet">
<style>
  :root {
    --bg: #2e2e2e;
    --card: #ffffff;
    --ink: #111111;
    --green: #8cc63f;
    --muted: #222222;
  }
  * { box-sizing: border-box; margin: 0; padding: 0; }
  html, body { width: 1200px; height: 875px; overflow: hidden; }
  body {
    background: var(--bg);
    font-family: "Poppins", sans-serif;
    position: relative;
  }
  .card {
    position: absolute;
    width: 530px;
    height: 303px;
    background: var(--card);
    top: 286px;
    overflow: hidden;
    box-shadow: 0 18px 40px rgba(0,0,0,.45);
  }
  .card--front { left: 50px; border-radius: 18px; }
  .card--back  { left: 620px; }

  .brand {
    display: flex;
    align-items: center;
    gap: 12px;
    position: absolute;
  }
  .brand__mark {
    width: 26px;
    height: 26px;
    background: var(--green);
    flex: none;
  }
  .brand__name {
    font-family: "Poppins", sans-serif;
    font-weight: 800;
    color: var(--ink);
    text-transform: uppercase;
    line-height: 1.05;
    letter-spacing: .5px;
  }
  .card--front .brand {
    left: 50%; top: 50%;
    transform: translate(-50%, -50%);
  }
  .card--front .brand__name { font-size: 34px; }
  .card--front .brand__mark { width: 34px; height: 34px; }

  .card--back .brand { left: 34px; top: 120px; }
  .card--back .brand__name { font-size: 21px; }
  .card--back .brand__mark { width: 22px; height: 22px; }

  .divider {
    position: absolute;
    left: 268px;
    top: 46px;
    width: 1.5px;
    height: 150px;
    background: var(--green);
  }
  .contact {
    position: absolute;
    left: 290px;
    top: 40px;
    color: var(--muted);
  }
  .contact__name {
    color: var(--green);
    font-weight: 600;
    font-size: 19px;
    line-height: 1.1;
  }
  .contact__title {
    font-size: 11px;
    margin-bottom: 10px;
  }
  .contact__list { list-style: none; font-size: 11px; line-height: 1.55; }
  .contact__list li { display: flex; align-items: center; gap: 7px; }
  .contact__list svg { width: 9px; height: 9px; fill: var(--green); flex: none; }
  .contact__address { font-size: 11px; line-height: 1.4; margin-top: 8px; }

  .swoosh { position: absolute; left: 0; top: 0; width: 530px; height: 303px; }
</style>
</head>
<body>

  <section class="card card--front" aria-label="Card front">
    <div class="brand">
      <span class="brand__mark"></span>
      <span class="brand__name">Ridgeline<br>Design + Build</span>
    </div>
  </section>

  <section class="card card--back" aria-label="Card back">
    <svg class="swoosh" viewBox="0 0 530 303" aria-hidden="true">
      <path d="M210 303 C320 290 450 230 530 150 L530 303 Z" fill="#111"/>
      <path d="M250 303 C350 285 460 225 530 175 L530 190 C460 240 360 295 270 303 Z" fill="#fff"/>
    </svg>

    <div class="brand">
      <span class="brand__mark"></span>
      <span class="brand__name">Ridgeline<br>Design + Build</span>
    </div>

    <div class="divider"></div>

    <div class="contact">
      <p class="contact__name">Daniel Porter</p>
      <p class="contact__title">Head contractor</p>
      <ul class="contact__list">
        <li><svg viewBox="0 0 10 10"><path d="M1 3c0-1 1-2 2-2h4c1 0 2 1 2 2v1H7V3H3v1H1zM2 5h6l1 4H1z"/></svg>555.014.2200</li>
        <li><svg viewBox="0 0 10 10"><path d="M3 0h4a1 1 0 0 1 1 1v8a1 1 0 0 1-1 1H3a1 1 0 0 1-1-1V1a1 1 0 0 1 1-1zm0 1.5v6h4v-6z"/></svg>555-014-2201</li>
        <li><svg viewBox="0 0 10 10"><path d="M0 2h10v6H0zm1 1v.4l4 2.4 4-2.4V3z"/></svg>info@rdb-build.com</li>
        <li><svg viewBox="0 0 10 10"><circle cx="5" cy="5" r="4.5"/></svg>www.rdb-build.com</li>
      </ul>
      <p class="contact__address">1420 Cedar Hollow Rd.<br>Pine Ridge, GA 30500</p>
    </div>
  </section>

</body>
</html>
```